BuildLinkHub.com Full Stationery Design

Business Card will have all info on it. Letterhead will not have name, title or mobile number. Keep general feeling very clean, using colors from the logo as accents.
Name:Dale Marchetti
Title:President
Phone: 1-800-555-0142
Cell: 306-555-0187
email: dale@buildlinkhub.example
website: www.buildlinkhub.example
Address:
PO Box 947
Pinecrest, SK
S0J2T0

Target Market(s)

Construction Business owners

Industry/Entity Type

Business

Contact Information for Business Card

Name:Dale Marchetti
Title:President
Phone: 1-800-555-0142
Cell: 306-555-0187
Address:
PO Box 947
Pinecrest, SK
S0J2T0

Font styles to use
Sans Serif

Requirements
Must have
• Clean look
Should not have
• Images or cartoon type characters or tools

```html
<!DOCTYPE html>
<html lang="en">
<head>
<meta charset="utf-8">
<title>BuildLinkHub.com Stationery</title>
<link href="https://fonts.googleapis.com/css2?family=Questrial&family=Open+Sans:wght@400;600&display=swap" rel="stylesheet">
<style>
  :root {
    --slate: #4b5b6f;
    --slate-light: #6b7f92;
    --orange: #ef5a2a;
    --paper: #ffffff;
    --backdrop: #e6e6e6;
    --ink: #3c3c3c;
    --rule: #8a8f96;
  }
  * { margin: 0; padding: 0; box-sizing: border-box; }
  html, body { width: 1200px; height: 1200px; overflow: hidden; }
  body {
    background: var(--backdrop);
    position: relative;
    font-family: "Open Sans", Arial, sans-serif;
    color: var(--ink);
  }
  .sheet { position: absolute; background: var(--paper); }

  .brand { display: flex; align-items: center; gap: 6px; white-space: nowrap; }
  .brand-mark { background: var(--orange); flex: none; }
  .brand-name { font-family: "Questrial", Arial, sans-serif; color: var(--slate); font-weight: 400; }

  /* Letterhead */
  .letterhead { left: 178px; top: 210px; width: 385px; height: 542px; }
  .letterhead .brand { position: absolute; left: 26px; top: 38px; }
  .letterhead .brand-mark { width: 18px; height: 18px; }
  .letterhead .brand-name { font-size: 15px; }
  .lh-contact { position: absolute; right: 25px; top: 40px; display: flex; gap: 6px; font-size: 5.6px; line-height: 8px; }
  .lh-address { text-align: right; padding-right: 5px; border-right: 0.6px solid var(--ink); }
  .icon { display: inline-block; width: 4px; height: 4px; background: var(--orange); border-radius: 50%; margin-right: 3px; vertical-align: middle; }
  .footer-rule { position: absolute; border-top: 0.8px solid var(--rule); }
  .footer-url { position: absolute; font-size: 6px; color: var(--ink); }
  .letterhead .footer-rule { left: 25px; right: 24px; top: 516px; }
  .letterhead .footer-url { right: 24px; top: 521px; }

  /* Folder / cover */
  .cover { left: 624px; top: 187px; width: 458px; height: 570px; }
  .cover .brand { position: absolute; left: 105px; top: 160px; gap: 12px; }
  .cover .brand-mark { width: 44px; height: 44px; }
  .cover .brand-name { font-size: 32px; }
  .cover .footer-rule { left: 18px; right: 18px; top: 546px; }
  .cover .footer-url { right: 18px; top: 551px; font-size: 7px; }

  /* Business card front */
  .card-front { left: 40px; top: 798px; width: 175px; height: 100px; }
  .card-front .brand { position: absolute; left: 10px; top: 14px; gap: 4px; }
  .card-front .brand-mark { width: 10px; height: 10px; }
  .card-front .brand-name { font-size: 8.5px; }
  .card-person { position: absolute; right: 10px; top: 53px; text-align: right; }
  .card-name { font-size: 6px; font-weight: 600; color: var(--slate); }
  .card-title { font-size: 3.6px; color: var(--orange); }
  .card-rule { position: absolute; left: 9px; right: 10px; top: 66px; border-top: 0.6px solid var(--rule); }
  .card-details { position: absolute; left: 9px; top: 70px; font-size: 3.6px; line-height: 5.2px; }
  .card-details .icon { width: 2.5px; height: 2.5px; margin-right: 2px; }
  .card-address { position: absolute; right: 10px; top: 80px; font-size: 3.6px; line-height: 4.8px; text-align: right; }

  /* Business card back */
  .card-back { left: 41px; top: 922px; width: 175px; height: 101px;
    background: linear-gradient(100deg, var(--slate), var(--slate-light)); display: flex; align-items: center; justify-content: center; }
  .card-back .brand { gap: 4px; }
  .card-back .brand-mark { width: 14px; height: 14px; }
  .card-back .brand-name { font-size: 9.5px; color: var(--paper); }

  /* Envelope front */
  .envelope-front { left: 257px; top: 813px; width: 428px; height: 204px; }
  .envelope-front .brand { position: absolute; left: 17px; top: 24px; }
  .envelope-front .brand-mark { width: 18px; height: 18px; }
  .envelope-front .brand-name { font-size: 13px; }
  .envelope-front .footer-rule { left: 17px; right: 16px; top: 184px; }
  .envelope-front .footer-url { right: 16px; top: 188px; }

  /* Envelope back */
  .envelope-back { left: 722px; top: 813px; width: 430px; height: 204px; }
  .envelope-flap { position: absolute; left: 0; top: 0; width: 430px; height: 70px; }
  .flap-mark { position: absolute; left: 198px; top: 12px; width: 34px; height: 34px; background: var(--orange); }
</style>
</head>
<body>

  <section class="sheet letterhead">
    <div class="brand"><span class="brand-mark"></span><span class="brand-name">BuildLinkHub.com</span></div>
    <div class="lh-contact">
      <div class="lh-address">PO Box 947 Pinecrest,<br>S0J2T0</div>
      <div><span class="icon"></span>1-800-555-0142<br><span class="icon"></span>dale@buildlinkhub.example</div>
    </div>
    <div class="footer-rule"></div>
    <div class="footer-url">www.buildlinkhub.example</div>
  </section>

  <section class="sheet cover">
    <div class="brand"><span class="brand-mark"></span><span class="brand-name">BuildLinkHub.com</span></div>
    <div class="footer-rule"></div>
    <div class="footer-url">www.buildlinkhub.example</div>
  </section>

  <section class="sheet card-front">
    <div class="brand"><span class="brand-mark"></span><span class="brand-name">BuildLinkHub.com</span></div>
    <div class="card-person">
      <div class="card-name">Dale Marchetti</div>
      <div class="card-title">President</div>
    </div>
    <div class="card-rule"></div>
    <div class="card-details">
      <div><span class="icon"></span>1-800-555-0142</div>
      <div><span class="icon"></span>306-555-0187</div>
      <div><span class="icon"></span>dale@buildlinkhub.example</div>
      <div><span class="icon"></span>www.buildlinkhub.example</div>
    </div>
    <div class="card-address">PO Box 947 Pinecrest,<br>S0J2T0</div>
  </section>

  <section class="sheet card-back">
    <div class="brand"><span class="brand-mark"></span><span class="brand-name">BuildLinkHub.com</span></div>
  </section>

  <section class="sheet envelope-front">
    <div class="brand"><span class="brand-mark"></span><span class="brand-name">BuildLinkHub.com</span></div>
    <div class="footer-rule"></div>
    <div class="footer-url">www.buildlinkhub.example</div>
  </section>

  <section class="sheet envelope-back">
    <svg class="envelope-flap" viewBox="0 0 430 70" aria-hidden="true">
      <defs>
        <linearGradient id="flapFill" x1="0" x2="1" y1="0" y2="0">
          <stop offset="0" stop-color="#4b5b6f"/>
          <stop offset="1" stop-color="#6b7f92"/>
        </linearGradient>
      </defs>
      <path d="M0 0 H430 L423 52 Q421 70 403 70 H27 Q9 70 7 52 Z" fill="url(#flapFill)"/>
    </svg>
    <div class="flap-mark"></div>
  </section>

</body>
</html>
```